BrindleStaffing Business Card Design

We are a staffing company finding positions for dedicated nurses and physicians.

Target Market(s)

Business Professionals

Industry/Entity Type

Staffing

Contact Information for Business Card

Gordon Pratley
Chairman
417 39th Avenue South
SAINT PETERSBURG FL 33712
813-555-4172 Mobile
813-555-8036 Fax
gpratley@brindlestaffing.com
www.brindlestaffing.com

Font styles to use
Sans Serif

Colors
fbee3e
f04a50
f37122

Requirements
Must have
• Logo Attached, see colors below. We'd like to see Yellow, Orange and Red.

```html
<!DOCTYPE html>
<html lang="en">
<head>
<meta charset="utf-8">
<title>BrindleStaffing Business Card</title>
<link rel="stylesheet" href="https://fonts.googleapis.com/css2?family=Poppins:wght@400;600&display=swap">
<style>
  :root {
    --page-bg: #e6e6e6;
    --card-white: #fbfbfb;
    --brand-yellow: #fbee3e;
    --brand-orange: #f37122;
    --brand-red: #f04a50;
    --ink: #3a3a3a;
    --dot-yellow: #fdf6bf;
    --dot-amber: #fde6bf;
    --dot-orange: #fcd9c3;
    --dot-red: #fbd3d4;
  }
  * { box-sizing: border-box; margin: 0; padding: 0; }
  html, body {
    width: 1200px; height: 582px; overflow: hidden;
    background: var(--page-bg);
    font-family: "Poppins", sans-serif;
  }
  .stage {
    position: relative; width: 1200px; height: 582px;
    display: flex; align-items: center; justify-content: center; gap: 60px;
  }
  .card {
    position: relative; width: 500px; height: 286px; overflow: hidden;
    box-shadow: 0 6px 18px rgba(0,0,0,0.12);
  }
  .card--front { background: var(--card-white); }
  .card--front::after {
    content: ""; position: absolute; left: 0; right: 0; bottom: 0; height: 6px;
    background: linear-gradient(90deg, var(--brand-yellow), var(--brand-orange), var(--brand-red));
  }
  .card--back {
    background: var(--brand-orange);
    display: flex; align-items: center; justify-content: center;
  }
  .wordmark {
    font-weight: 600; letter-spacing: -0.5px; white-space: nowrap;
  }
  .card--front .wordmark {
    position: absolute; top: 26px; right: 30px;
    font-size: 26px; color: var(--brand-orange);
  }
  .card--back .wordmark { font-size: 44px; color: #ffffff; }
  .dot-row {
    position: absolute; left: 34px; top: 80px;
    display: flex; gap: 14px;
  }
  .dot-row span { width: 24px; height: 24px; border-radius: 50%; }
  .dot-row span:nth-child(1) { background: var(--dot-yellow); }
  .dot-row span:nth-child(2) { background: var(--dot-amber); }
  .dot-row span:nth-child(3) { background: var(--dot-orange); }
  .dot-row span:nth-child(4) { background: var(--dot-red); }
  .identity { position: absolute; left: 34px; top: 114px; }
  .identity__name {
    font-weight: 600; font-size: 21px; color: var(--brand-red); line-height: 1.1;
  }
  .identity__title { font-size: 11px; color: var(--ink); margin-top: 2px; }
  .address { margin-top: 10px; font-size: 10px; line-height: 1.4; color: var(--ink); }
  .contacts { margin-top: 8px; list-style: none; font-size: 10px; color: var(--ink); }
  .contacts li { display: flex; align-items: center; gap: 7px; line-height: 1.5; }
  .contacts svg { width: 9px; height: 9px; fill: var(--brand-orange); flex: none; }
</style>
</head>
<body>
<main class="stage">
  <section class="card card--front" aria-label="Business card front">
    <div class="wordmark">BrindleStaffing</div>
    <div class="dot-row" aria-hidden="true"><span></span><span></span><span></span><span></span></div>
    <div class="identity">
      <h1 class="identity__name">Gordon Pratley</h1>
      <p class="identity__title">Chairman</p>
      <p class="address">417 39th Avenue South<br>SAINT PETERSBURG FL 33712</p>
      <ul class="contacts">
        <li>
          <svg viewBox="0 0 10 10" aria-hidden="true"><path d="M2 0.5 L3.8 2.6 L2.9 3.7 Q4 6 6.3 7.1 L7.4 6.2 L9.5 8 L8.5 9.5 Q3.5 9 0.5 1.5 Z"/></svg>
          813-555-4172 Mobile
        </li>
        <li>
          <svg viewBox="0 0 10 10" aria-hidden="true"><path d="M2.5 0.5 H7.5 V3.5 H2.5 Z M0.5 4 H9.5 V8 H7.5 V9.5 H2.5 V8 H0.5 Z"/></svg>
          813-555-8036 Fax
        </li>
        <li>
          <svg viewBox="0 0 10 10" aria-hidden="true"><path d="M0.5 2 H9.5 V8.5 H0.5 Z M0.5 2 L5 5.5 L9.5 2" stroke="#fbfbfb" stroke-width="0.8"/></svg>
          gpratley@brindlestaffing.com
        </li>
        <li>
          <svg viewBox="0 0 10 10" aria-hidden="true"><circle cx="5" cy="5" r="4.5"/></svg>
          www.brindlestaffing.com
        </li>
      </ul>
    </div>
  </section>
  <section class="card card--back" aria-label="Business card back">
    <div class="wordmark">BrindleStaffing</div>
  </section>
</main>
</body>
</html>
```